International sourcing and trading company needs website design on Squarespace

We are international sourcing and trading company based in Brisbane ,Australia. We help our clients to source any products they need to economically produce overseas and we manage the whole production process for them. We want our visual identity to show that we are professional, dynamic, efficient and are able to source any product around the world. Our website will be simply information and advertising website , no ecommerce or any transactions. Please see attached our company logo. We would like our website to have the following sections/pages:

1.Main banner with a simple slogan/sentence to introduce what we do: Let us handle the overseas sourcing and production for you.

2. Post-Covid sourcing and producing management: introducing our competence on managing sourcing and overseas production under the travel restriction and the growing tension on global trading. We will supply the exact wording later on;

3. About us: We are a professional team with mature global sourcing and trading experience. We have branch office in Hong Kong and local resources around all areas in China , India and other Asian countries. Our working flow is: received inquiry->start sourcing->(in 1 week time)give price and delivery date on inquired products or further information->(if needed)arrange samples for clients->(if samples and orders are confirmed)deliver Pre-production sample-> kick-off production->arrange inspection through the whole production-> (if need) arrange shipment to client. We would like to show the work flow in a personalized way , eg. personalize icons etc.;

4. What kind of product we can source and produce: our business is sourcing and managing manufacture overseas for our clients, product categories mainly, but not just, are clothing, shoes , bags, clothing accessories, makeup accessories, festival or promotional gifts etc. all kind of daily use products . We basically are able to source and manage production of every kind of products with no limits. We would like this page to be particularly personalized in a way to give impression to whom browse our website feel free to send inquiry of any kind of production to us and they can trust us that we will do our job professionally and dynamically. We are thinking of using some icons of daily use products to show our sourcing category , it's just our though so please feel free to propose any other ides that you think is more suitable from the point of view of professional designer.

5. Start an enquiry: here we need to land on a questionary page to let who would like to make en enquiry leave the main information , including:
-Name & Sir name:
-Company name:
-Contact email:
-Phone numer:
-Enquired product:
-Upload image:
-Preferred or previous production country:
-Preferred price: FOB, CIF, DDP
-If CIF or DDP where the arrival port/airport will be:
-Preferred delivery time:
-Preferred transportation: by air, by sea, by train
- Other specific requires:

6: Contact us: We will supply contact info later on

Above are our thoughts but please feel free to propose any other ideas that you think should be more suitable for us. We trust your expertise and professional opinions.

Wholesalers and retailers who need to produce their products overseas (mainly in China and other countries in Asia)

• We think it will be nice to show information in simple and comprehensive icons instead of piles of words. We will want our website neat, easy to understand what we do and professional. However this is just our thought so please feel free to propose any other ideas that you think is more suitable from the point of view of professional designer.

```html
<!DOCTYPE html>
<html lang="en">
<head>
<meta charset="utf-8">
<title>Corvalis – Sourcing and Trading</title>
<link href="https://fonts.googleapis.com/css2?family=Montserrat:wght@700&family=Roboto:wght@400;500;700&display=swap" rel="stylesheet">
<style>
:root{
  --teal:#2fa0b6;
  --orange:#f39a33;
  --ink:#1d1d1d;
  --text:#555;
  --grey-bg:#f1f1f1;
  --footer:#0d0d0d;
  --white:#fff;
}
*{margin:0;padding:0;box-sizing:border-box}
html,body{width:1200px;height:3712px;overflow:hidden}
body{position:relative;font-family:'Roboto',Arial,sans-serif;color:var(--text);background:var(--white)}

/* header */
.site-header{position:absolute;left:0;top:0;width:1200px;height:98px;background:var(--white)}
.brand{position:absolute;left:172px;top:26px;display:flex;align-items:center;gap:12px}
.brand-dot{width:40px;height:40px;border-radius:50%;background:var(--teal)}
.brand-name{font-family:'Roboto',Arial,sans-serif;font-weight:500;font-size:32px;color:var(--orange);letter-spacing:-.5px}
.follow{position:absolute;left:836px;top:24px;font-size:10px;font-weight:700;color:var(--ink);letter-spacing:.3px}
.social{position:absolute;top:18px;width:24px;height:24px;border-radius:50%;background:var(--orange)}
.social.alt{background:var(--teal)}
.main-nav{position:absolute;top:63px;left:497px;font-size:14px;font-weight:500;color:var(--ink)}
.main-nav a{color:inherit;text-decoration:none;position:absolute;white-space:nowrap}
.main-nav a.active{color:var(--teal)}

/* hero */
.hero-art{position:absolute;left:0;top:98px}
.hero-title{position:absolute;left:0;width:1200px;top:278px;text-align:center;font-family:'Montserrat',Arial,sans-serif;font-weight:700;font-size:76px;color:var(--white);letter-spacing:-1px}
.hero-sub{position:absolute;left:0;width:1200px;top:370px;text-align:center;font-size:25px;line-height:31px;color:var(--white)}
.slider-arrow{position:absolute;top:347px;width:36px;height:36px;border:2px solid var(--white);border-radius:50%}
.slider-arrow svg{position:absolute;left:9px;top:9px}

/* section titles */
.section-title{position:absolute;left:0;width:1200px;text-align:center;font-weight:700;font-size:42px;letter-spacing:-.5px}
.section-title .a{color:var(--teal)} .section-title .b{color:var(--orange)}

/* about */
.about-visual{position:absolute;left:158px;top:850px;width:452px;height:362px}
.about-title{position:absolute;left:633px;top:872px;font-weight:700;font-size:42px;letter-spacing:-.5px}
.about-title .a{color:var(--teal)} .about-title .b{color:var(--orange)}
.about-text{position:absolute;left:633px;top:933px;width:395px;font-size:12.5px;line-height:19.5px}
.btn{position:absolute;display:flex;align-items:center;justify-content:center;border-radius:24px;font-size:13px;font-weight:500;color:var(--white);text-transform:uppercase}
.btn-read{left:627px;top:1128px;width:144px;height:46px;background:var(--orange)}

/* products */
.products-bg{position:absolute;left:0;top:1298px;width:1200px;height:500px;background:var(--grey-bg)}
.product-photo{position:absolute;top:1430px;width:272px;height:166px}
.product-card{position:absolute;top:1565px;width:250px;height:122px;background:var(--white);border-radius:3px;box-shadow:0 1px 4px rgba(0,0,0,.08);text-align:center;padding:0 14px}
.product-card h3{margin-top:22px;font-size:15px;font-weight:500;color:var(--ink)}
.product-card p{margin-top:9px;font-size:12px;line-height:19px;color:var(--text)}
.carousel-chev{position:absolute;top:1536px}

/* promo bands */
.band{position:absolute;left:0}
.band-heading{position:absolute;left:0;width:1200px;text-align:center;font-weight:700;font-size:30px;line-height:38px;color:var(--white);letter-spacing:-.3px}
.band-text{position:absolute;left:0;width:1200px;text-align:center;font-size:13px;line-height:19.5px;color:var(--white)}
.btn-contact{left:508px;top:2040px;width:184px;height:38px;background:var(--orange);border:2px solid var(--white)}
.btn-enquiry{left:508px;top:3124px;width:184px;height:38px;background:var(--teal);border:2px solid var(--white)}

/* blog */
.blog-photo{position:absolute}
.blog-card{position:absolute;background:var(--white);box-shadow:0 1px 5px rgba(0,0,0,.1);padding:20px 22px}
.blog-card h3{font-size:18px;font-weight:500;line-height:22px;color:var(--teal)}
.blog-card p{margin-top:10px;font-size:12px;line-height:17px;color:var(--text)}

/* footer */
.footer-brand{position:absolute;left:0;width:1200px;top:3300px;display:flex;justify-content:center;align-items:center;gap:14px}
.footer-col{position:absolute;top:3424px}
.footer-col h4{font-size:13px;font-weight:700;color:var(--teal);text-transform:uppercase;margin-bottom:12px}
.footer-col li{list-style:none;font-size:12px;line-height:19.5px;color:#555}
.contact-row{position:relative;padding-left:36px;font-size:12px;line-height:19.5px;color:#555;margin-bottom:14px}
.contact-row svg{position:absolute;left:0;top:2px}
.footer-rule{position:absolute;left:172px;top:3653px;width:856px;height:1px;background:#2a2a2a}
.copyright{position:absolute;left:0;width:1200px;top:3672px;text-align:center;font-size:13px;color:var(--orange)}
</style>
</head>
<body>

<header class="site-header">
  <div class="brand"><span class="brand-dot"></span><span class="brand-name">Corvalis</span></div>
  <span class="follow">FOLLOW US:</span>
  <span class="social" style="left:912px"></span>
  <span class="social alt" style="left:942px"></span>
  <span class="social" style="left:972px"></span>
  <span class="social alt" style="left:1003px"></span>
  <nav class="main-nav">
    <a class="active" style="left:0">Home</a>
    <a style="left:63px">Post-Covid</a>
    <a style="left:158px">About us</a>
    <a style="left:240px">Products</a>
    <a style="left:327px">Start an enquiry</a>
    <a style="left:458px">Contact Us</a>
  </nav>
</header>

<svg class="hero-art" width="1200" height="700" viewBox="0 98 1200 700">
  <defs>
    <linearGradient id="heroSky" x1="0" y1="0" x2="0" y2="1">
      <stop offset="0" stop-color="#2c4350"/>
      <stop offset=".5" stop-color="#4c5a5e"/>
      <stop offset=".75" stop-color="#7a6a4e"/>
      <stop offset="1" stop-color="#3a3a34"/>
    </linearGradient>
  </defs>
  <g role="img" aria-label="City skyline with a steel bridge over a river at sunset">
    <rect x="0" y="98" width="1200" height="640" fill="url(#heroSky)"/>
  </g>
  <path d="M0 668 Q600 800 1200 588 L1200 800 L0 800 Z" fill="var(--orange)"/>
  <path d="M0 705 Q600 825 1200 620 L1200 800 L0 800 Z" fill="var(--white)"/>
</svg>
<h1 class="hero-title">WHAT WE DO</h1>
<p class="hero-sub">Let us handle the overseas sourcing<br>and production for you.</p>
<span class="slider-arrow" style="left:27px"><svg width="14" height="14" viewBox="0 0 14 14"><path d="M9 2 L4 7 L9 12" stroke="#fff" stroke-width="2" fill="none"/></svg></span>
<span class="slider-arrow" style="left:1122px"><svg width="14" height="14" viewBox="0 0 14 14"><path d="M5 2 L10 7 L5 12" stroke="#fff" stroke-width="2" fill="none"/></svg></span>

<svg class="about-visual" viewBox="0 0 452 362" role="img" aria-label="Round collage of city views at dusk">
  <defs>
    <linearGradient id="globeFill" x1="0" y1="0" x2="0" y2="1">
      <stop offset="0" stop-color="#7fa7c0"/>
      <stop offset=".5" stop-color="#c98a55"/>
      <stop offset="1" stop-color="#2a3550"/>
    </linearGradient>
  </defs>
  <circle cx="180" cy="181" r="178" fill="url(#globeFill)"/>
</svg>
<h2 class="about-title"><span class="a">ABOUT</span> <span class="b">US</span></h2>
<p class="about-text">Lorem ipsum dolor sit amet, consectetur adipiscing elit, sed eiusmod tempor incididunt ut labore et dolore magna aliqua. Ut enim ad minim veniam, quis nostrud exercitation ullamco laboris nisi ut aliquip ex ea commodo consequat. Duis aute irure dolor in reprehenderit voluptate velit esse cillum dolore eu fugiat nulla pariatur. Excepteur sint occaecat cupidatat non proident, sunt in culpa qui officia deserunt mollit anim id est laborumonsequat. Duis aute irure dolor in reprehenderit voluptate velit esse cillum dolore eu fugiat nulla pariatur. Excepteur sint occaecat cupidatat non proident, sunt in culpa qu</p>
<span class="btn btn-read">Read More</span>

<div class="products-bg"></div>
<h2 class="section-title" style="top:1346px"><span class="a">OUR</span> <span class="b">PRODUCTS</span></h2>
<div class="product-photo" role="img" aria-label="Clothes on hangers" style="left:172px;background:linear-gradient(135deg,#c9a7a0,#8a4a40)"></div>
<div class="product-photo" role="img" aria-label="Pair of white boots" style="left:464px;background:linear-gradient(135deg,#7d8fa0,#3c4650)"></div>
<div class="product-photo" role="img" aria-label="Orange handbag" style="left:756px;background:linear-gradient(135deg,#b9bcc2,#d9642a)"></div>
<div class="product-card" style="left:183px"><h3>CLOTHING</h3><p>Lorem ipsum dolor sit consectetur adipiscing elit, sed do eiusmod tempor incididunt ut labore</p></div>
<div class="product-card" style="left:475px"><h3>SHOES</h3><p>Lorem ipsum dolor sit consectetur adipiscing elit, sed do eiusmod tempor incididunt ut labore</p></div>
<div class="product-card" style="left:767px"><h3>BAGS</h3><p>Lorem ipsum dolor sit consectetur adipiscing elit, sed do eiusmod tempor incididunt ut labore</p></div>
<svg class="carousel-chev" style="left:114px" width="22" height="38" viewBox="0 0 22 38"><path d="M18 3 L4 19 L18 35" stroke="#999" stroke-width="4" fill="none"/></svg>
<svg class="carousel-chev" style="left:1064px" width="22" height="38" viewBox="0 0 22 38"><path d="M4 3 L18 19 L4 35" stroke="#999" stroke-width="4" fill="none"/></svg>

<svg class="band" style="top:1725px" width="1200" height="510" viewBox="0 0 1200 510" role="img" aria-label="Teal-tinted photo of shoppers browsing clothing racks">
  <defs><linearGradient id="tealBand" x1="0" y1="0" x2="1" y2="1"><stop offset="0" stop-color="#2b9ab0"/><stop offset="1" stop-color="#4ab0c2"/></linearGradient></defs>
  <path d="M0 5 Q600 130 1200 5 L1200 505 Q600 380 0 505 Z" fill="url(#tealBand)"/>
</svg>
<h2 class="band-heading" style="top:1872px">Lorem ipsum dolor sit amet, consectetur adipisci<br>ng elit, sed do eiusmod tempor incididun</h2>
<p class="band-text" style="top:1956px">Lorem ipsum dolor sit amet, consectetur adipiscing elit, sed do eiusmod tempor incididunt ut labore et<br>dolore magna aliqua. Ut enim ad minim veniam &nbsp;quis nostrud exercitation ullamco laboris nisi ut aliquip<br>ex ea commodo consequat. Duis aute irure dolor in reprehenderit in voluptate velit ess</p>
<span class="btn btn-contact">Contact Us Now</span>

<h2 class="section-title" style="top:2236px"><span class="a">LATEST</span> <span class="b">BLOG</span></h2>
<div class="blog-photo" role="img" aria-label="Two women shopping at a clothing rack" style="left:172px;top:2323px;width:508px;height:352px;background:linear-gradient(135deg,#3a3a3e,#8a7a6a 60%,#c9b69a)"></div>
<div class="blog-card" style="left:212px;top:2577px;width:445px;height:148px"><h3>Lorem ipsum dol amet,or incididun<br>amet,or incididunt utt ut labo</h3><p>Lorem ipsum dolor sit amet, consectetur adipiscing elit, sed do eiusmod tempor incididunt ut labore et dolore magna aliqua.<br>Ut enim ad minim veniam, quis nostrud exercitation</p></div>
<div class="blog-photo" role="img" aria-label="Makeup brushes" style="left:696px;top:2323px;width:175px;height:195px;background:linear-gradient(135deg,#2a2326,#8a5a50)"></div>
<div class="blog-photo" role="img" aria-label="Black leather shoe" style="left:696px;top:2535px;width:175px;height:193px;background:linear-gradient(135deg,#1e1e20,#5a2a2a)"></div>
<div class="blog-card" style="left:778px;top:2350px;width:250px;height:142px"><h3>Lorem ipsum dol amet,<br>or incididunt ut labo</h3><p>Lorem ipsum dolor sit amet, consect etur adipiscing elit, sed do eiusmod tempor incididunt ut labo</p></div>
<div class="blog-card" style="left:778px;top:2560px;width:250px;height:142px"><h3>Lorem ipsum dol amet,<br>or incididunt ut labo</h3><p>Lorem ipsum dolor sit amet, consect etur adipiscing elit, sed do eiusmod tempor incididunt ut labo</p></div>

<svg class="band" style="top:2805px" width="1200" height="907" viewBox="0 0 1200 907">
  <defs><linearGradient id="orangeBand" x1="0" y1="0" x2="0" y2="1"><stop offset="0" stop-color="#f39a33"/><stop offset="1" stop-color="#e88d24"/></linearGradient></defs>
  <g role="img" aria-label="Orange-tinted aerial city view">
    <path d="M0 5 Q600 130 1200 5 L1200 600 L0 600 Z" fill="url(#orangeBand)"/>
  </g>
  <path d="M0 510 Q600 360 1200 510 L1200 907 L0 907 Z" fill="var(--footer)"/>
</svg>
<h2 class="band-heading" style="top:2955px">Lorem ipsum dolor sit amet, consectetur adipisci<br>ng elit, sed do eiusmod tempor incididun</h2>
<p class="band-text" style="top:3039px">Lorem ipsum dolor sit amet, consectetur adipiscing elit, sed do eiusmod tempor incididunt ut labore et<br>dolore magna aliqua. Ut enim ad minim veniam &nbsp;quis nostrud exercitation ullamco laboris nisi ut aliquip<br>ex ea commodo consequat. Duis aute irure dolor in reprehenderit in voluptate velit ess</p>
<span class="btn btn-enquiry">Enquiry Now</span>

<footer>
  <div class="footer-brand"><span class="brand-dot" style="width:50px;height:50px"></span><span class="brand-name" style="font-size:40px">Corvalis</span></div>

  <div class="footer-col" style="left:172px;width:220px">
    <h4>Contact</h4>
    <div class="contact-row"><svg width="18" height="20" viewBox="0 0 18 20"><path d="M9 19 C4 13 2 10 2 7 A7 7 0 0 1 16 7 C16 10 14 13 9 19 Z" stroke="var(--teal)" stroke-width="1.5" fill="none"/><circle cx="9" cy="7" r="2.5" stroke="var(--teal)" stroke-width="1.5" fill="none"/></svg>42 Harbour Lane,<br>Riverton QLD</div>
    <div class="contact-row"><svg width="20" height="20" viewBox="0 0 20 20"><path d="M4 2 L8 6 L6 9 Q9 14 12 15 L14 13 L18 17 L15 19 Q6 17 2 6 Z" stroke="var(--teal)" stroke-width="1.5" fill="none"/></svg>0 400 123 456 78<br>0 400 987 654 32</div>
    <div class="contact-row"><svg width="22" height="16" viewBox="0 0 22 16"><rect x="1" y="1" width="20" height="14" stroke="var(--teal)" stroke-width="1.5" fill="none"/><path d="M1 1 L11 9 L21 1" stroke="var(--teal)" stroke-width="1.5" fill="none"/></svg>hello@corvalis.test<br>team@corvalis.test</div>
  </div>
  <div class="footer-col" style="left:439px">
    <h4>Company</h4>
    <ul><li>Lorem ipsum dolo</li><li>Fusce eget leo tincid</li><li>Donec consequat</li><li>Praesent elementum</li><li>Jmauris posueret</li><li>Aenean a ex eu lectu</li><li>Donec consequa</li></ul>
  </div>
  <div class="footer-col" style="left:666px">
    <h4>Advantages</h4>
    <ul><li>Lorem ipsum dolo</li><li>Fusce eget leo tincid</li><li>Donec consequat</li><li>Praesent elementum</li><li>Jmauris posueret</li><li>Donec consequa</li></ul>
  </div>
  <div class="footer-col" style="left:885px">
    <h4>Other Links</h4>
    <ul><li>Lorem ipsum dolo</li><li>Consecteturipiscinit</li><li>Fusce eget leo tincid</li><li>Praesent elementum</li><li>Jmauris posueret</li><li>Donec consequa</li></ul>
  </div>
  <div class="footer-rule"></div>
  <p class="copyright">Copyright 2020 Corvalis. All Rights Reserved</p>
</footer>

</body>
</html>
```